Business Card for Coastal Tundrabridge Advisory

We need a business card for Coastal Tundrabridge Advisory. The company website address is provided below. The company logo is attached. We provide specialized permafrost services to the mining, transportation, and oil & gas industries. The card should be prepared for:
Matthias Korhonen, PhD.
Coastal Tundrabridge Advisory
PO Box 418259
Quillwater, Alaska 99642
Direct: +1-907-555-0143
Email: mkorhonen@tundrabridgeadvisory.example
Website: www.coastaltundrabridgeadvisory.example

```html
<!DOCTYPE html>
<html lang="en">
<head>
<meta charset="utf-8">
<title>Coastal Tundrabridge Advisory — Business Card</title>
<link href="https://fonts.googleapis.com/css2?family=Montserrat:wght@400;500;700&display=swap" rel="stylesheet">
<style>
  :root {
    --ink: #101923;
    --ink-soft: #1c2733;
    --paper: #ffffff;
    --stage: #d9dbde;
    --rule: #2a323c;
  }
  * { margin: 0; padding: 0; box-sizing: border-box; }
  html, body { width: 1200px; height: 1200px; overflow: hidden; }
  body {
    background: var(--stage);
    font-family: "Montserrat", sans-serif;
    color: var(--ink);
    position: relative;
  }
  .card {
    position: absolute;
    left: 170px;
    width: 860px;
    height: 491px;
    overflow: hidden;
    box-shadow: 0 10px 30px rgba(0,0,0,0.18);
  }
  .card--back { top: 80px; background: var(--ink); }
  .card--front { top: 629px; background: var(--ink); }

  .back-pattern {
    position: absolute;
    inset: 0;
    background: linear-gradient(120deg, rgba(190,196,204,0.28) 0%, rgba(120,128,138,0.12) 30%, rgba(16,25,35,0) 60%, rgba(40,50,62,0.25) 100%);
  }
  .back-brand {
    position: absolute;
    left: 0; right: 0;
    top: 300px;
    text-align: center;
    color: var(--paper);
    font-weight: 700;
    font-size: 30px;
    letter-spacing: 1px;
  }

  .front-shape { position: absolute; inset: 0; }
  .front-brand {
    position: absolute;
    left: 56px;
    top: 222px;
    width: 270px;
    font-weight: 700;
    font-size: 24px;
    line-height: 1.2;
    color: var(--ink);
  }
  .front-divider {
    position: absolute;
    left: 345px;
    top: 150px;
    width: 1.5px;
    height: 230px;
    background: var(--rule);
  }
  .contact {
    position: absolute;
    left: 372px;
    top: 140px;
    color: var(--ink);
  }
  .contact__name { font-weight: 700; font-size: 25px; }
  .contact__title { font-weight: 400; font-size: 15px; margin-top: 2px; }
  .contact__address { font-size: 15px; line-height: 1.35; margin-top: 18px; }
  .contact__list { list-style: none; margin-top: 20px; }
  .contact__item {
    display: flex;
    align-items: center;
    gap: 14px;
    font-size: 14.5px;
    margin-bottom: 12px;
  }
  .contact__icon { width: 15px; height: 15px; flex: none; }
</style>
</head>
<body>

  <section class="card card--back" aria-label="Card back">
    <div class="back-pattern" role="img" aria-label="Faint repeating company-name pattern in silver fading to black"></div>
    <div class="back-brand">Coastal Tundrabridge Advisory</div>
  </section>

  <section class="card card--front" aria-label="Card front">
    <svg class="front-shape" viewBox="0 0 860 491" width="860" height="491" aria-hidden="true">
      <path fill="#ffffff" d="M0,0 L560,0 C760,0 860,120 860,300 L860,491 L300,491 C120,491 0,400 0,260 Z"/>
    </svg>

    <div class="front-brand">Coastal Tundrabridge Advisory</div>
    <div class="front-divider"></div>

    <div class="contact">
      <p class="contact__name">Matthias Korhonen, PhD.</p>
      <p class="contact__title">Managing Director</p>
      <p class="contact__address">PO Box 418259<br>Quillwater, Alaska 99642</p>
      <ul class="contact__list">
        <li class="contact__item">
          <svg class="contact__icon" viewBox="0 0 24 24" aria-hidden="true"><path fill="#101923" d="M6.6 10.8a15.1 15.1 0 0 0 6.6 6.6l2.2-2.2a1 1 0 0 1 1-.25 11.4 11.4 0 0 0 3.6.57 1 1 0 0 1 1 1V20a1 1 0 0 1-1 1A17 17 0 0 1 3 4a1 1 0 0 1 1-1h3.5a1 1 0 0 1 1 1c0 1.25.2 2.45.57 3.57a1 1 0 0 1-.25 1z"/></svg>
          <span>+1-907-555-0143</span>
        </li>
        <li class="contact__item">
          <svg class="contact__icon" viewBox="0 0 24 24" aria-hidden="true"><path fill="#101923" d="M2 5h20v14H2z"/><path fill="none" stroke="#fff" stroke-width="1.8" d="M2.5 5.5 12 13l9.5-7.5"/></svg>
          <span>mkorhonen@tundrabridgeadvisory.example</span>
        </li>
        <li class="contact__item">
          <svg class="contact__icon" viewBox="0 0 24 24" aria-hidden="true"><circle cx="12" cy="12" r="10" fill="#101923"/><path fill="none" stroke="#fff" stroke-width="1.4" d="M2 12h20M12 2c3 3 3 17 0 20M12 2c-3 3-3 17 0 20"/></svg>
          <span>www.coastaltundrabridgeadvisory.example</span>
        </li>
      </ul>
    </div>
  </section>

</body>
</html>
```